WordPress Design for both website and landing page for an expert

I need a clean and stylish design for my new website. I work as an expert (see attached file WHY HOW WHAT), my product is expert opinion (reports) for company evaluations You can use all of the attached pictures colored or black / white. The person is me, you can add other pictures, if you want. The design should be clean and stylish, so you could use white, black, gray, silver and / or one additional color. I have added an idea about my website, see attached file CONCEPT WEBSITE If you have any more information, please do not hesitate to contact us 'Hesitate to ask me ...

```html
<!DOCTYPE html>
<html lang="de">
<head>
<meta charset="utf-8">
<title>Lukas Arnhold – Expert for Company Valuations</title>
<link href="https://fonts.googleapis.com/css2?family=Montserrat:wght@300;400;600;700&family=Open+Sans:wght@400;600&display=swap" rel="stylesheet">
<style>
:root{
  --black:#000;
  --ink:#222;
  --text:#555;
  --muted:#888;
  --blue:#1f4fa0;
  --navy:#173f8a;
  --line:#d8d8d8;
  --grey-bg:#e6e6e6;
  --icon:#555;
  --white:#fff;
}
*{margin:0;padding:0;box-sizing:border-box}
html,body{width:1200px;height:4369px;overflow:hidden;background:var(--white)}
body{font-family:"Open Sans",Arial,sans-serif;color:var(--text);position:relative}
section,header,footer{position:relative;width:1200px;overflow:hidden}
.abs{position:absolute}
.heading{font-family:"Montserrat",sans-serif;font-weight:400;color:var(--ink);letter-spacing:1px}
.rule{position:absolute;height:3px;background:var(--blue)}
.small{font-size:12px;line-height:26px;color:var(--text)}

/* header */
.site-header{height:105px;background:var(--black)}
.brand{left:112px;top:38px;font-family:"Montserrat",sans-serif;font-weight:400;font-size:20px;letter-spacing:4px;color:var(--white)}
.nav{top:45px;font-family:"Montserrat",sans-serif;font-weight:600;font-size:12px;color:var(--white)}
.nav.active{color:#3a7bd5}

/* hero */
.hero{height:568px;background:linear-gradient(180deg,#2e68c2 0%,#3a78cf 35%,#1f3c6e 62%,#2a2c4a 80%,#1a2a4c 100%)}
.hero-title{width:100%;text-align:center;top:70px;font-family:"Montserrat",sans-serif;font-weight:700;font-size:31px;color:var(--white);letter-spacing:.5px}
.hero-sub{width:100%;text-align:center;top:122px;font-family:"Montserrat",sans-serif;font-weight:300;font-size:28px;line-height:42px;color:var(--white)}

/* why choose us */
.why{height:513px}
.why .heading{width:100%;text-align:center;top:58px;font-size:31px}
.card{top:148px;width:309px;height:300px;border:1px solid var(--line);text-align:center}
.card .badge{position:absolute;left:96px;top:27px;width:116px;height:116px;border-radius:50%;background:var(--icon)}
.card h3{position:absolute;width:100%;top:164px;font-family:"Montserrat",sans-serif;font-weight:400;font-size:17px;color:var(--ink);letter-spacing:1px}
.card p{position:absolute;left:30px;right:30px;top:200px;font-size:12px;line-height:26px}

/* reasons */
.reasons{height:495px;background:linear-gradient(90deg,#e4e4e4 0%,#ececec 50%,#f4f4f4 100%)}
.reasons .photo{right:0;top:0;width:560px;height:495px;background:linear-gradient(90deg,rgba(236,236,236,0) 0%,#d9d6d2 35%,#bfb9b2 65%,#a9a39c 100%)}
.reasons h2{left:111px;top:98px;font-family:"Montserrat",sans-serif;font-weight:600;font-size:34px;color:#333;letter-spacing:.5px}
.reasons h4{left:111px;top:147px;font-family:"Montserrat",sans-serif;font-weight:400;font-size:23px;color:#444;letter-spacing:.5px}
.reason{left:111px;width:495px;height:50px;border:1px solid #bbb;background:rgba(255,255,255,.15);padding:0 16px;line-height:48px;font-size:12px;color:var(--text)}
.reason b{font-family:"Montserrat",sans-serif;font-weight:400;font-size:17px;color:#333;margin-right:4px}

/* quality */
.quality{height:446px}
.quality .art{left:146px;top:81px;width:378px;height:335px;border-radius:24px;background:radial-gradient(circle at 50% 60%,#8a77e8 0%,#b9adf3 45%,#fff 75%)}
.quality h2{left:568px;top:76px;font-size:31px}
.quality .p1{left:568px;top:147px;width:540px}
.btn-outline{left:568px;height:38px;border:1px solid var(--blue);font-family:"Montserrat",sans-serif;font-weight:600;font-size:11px;color:var(--navy);text-align:center;line-height:36px}
.quality .p2{left:568px;top:264px;width:540px}

/* about */
.about{height:635px;background:var(--grey-bg)}
.about .portrait{left:146px;top:67px;width:442px;height:495px;background:linear-gradient(180deg,#cfcfcf 0%,#9a9a9a 50%,#3c3c3c 100%)}
.about .card{left:530px;top:134px;width:530px;height:375px;background:var(--white);border:none;box-shadow:0 4px 18px rgba(0,0,0,.12);text-align:left}
.about h2{left:40px;top:40px;font-size:33px}
.about .bar{left:40px;top:92px;width:115px}
.about .txt{left:40px;right:40px;font-size:12px;line-height:26px}

/* what how why */
.circles{height:533px}
.circles svg{left:150px;top:70px}
.wh h2{font-size:33px}
.wh{left:600px}
.wh p{font-size:12px;line-height:26px}

/* contact */
.contact{height:445px;background:linear-gradient(90deg,#f3f3f3 0%,#f7f7f7 50%,#e2e2e2 100%)}
.contact h2{width:100%;text-align:center;top:38px;font-size:31px}
.contact .intro{width:100%;text-align:center;top:100px;font-size:12px;line-height:26px}
.field{background:var(--white);border:1px solid #ccc;font-size:12px;color:#444;padding:13px 16px}
.submit{left:530px;top:364px;width:140px;height:41px;background:var(--navy);color:var(--white);font-family:"Montserrat",sans-serif;font-weight:600;font-size:13px;text-align:center;line-height:41px}

/* promise */
.promise{height:417px;text-align:center}
.promise .mark{width:100%;top:90px;font-family:"Montserrat",sans-serif;font-weight:400;font-size:40px;letter-spacing:8px;color:#6a6a6a}
.promise h3{width:100%;top:248px;font-family:"Montserrat",sans-serif;font-weight:400;font-size:27px;color:var(--ink);letter-spacing:1px}
.promise p{width:100%;top:295px;font-size:17px;line-height:28px;color:#333}

/* footer */
.site-footer{height:212px;background:var(--black);text-align:center}
.site-footer .mark{width:100%;top:58px;font-family:"Montserrat",sans-serif;font-weight:400;font-size:24px;letter-spacing:6px;color:#cfcfcf}
.site-footer .copy{width:100%;top:160px;font-size:12px;color:#ddd}
.site-footer .tag{left:1098px;top:184px;font-size:11px;color:#ddd}
</style>
</head>
<body>

<header class="site-header">
  <div class="abs brand">LUKAS ARNHOLD</div>
  <nav>
    <span class="abs nav active" style="left:482px">HOME</span>
    <span class="abs nav" style="left:573px">WHAT I DO</span>
    <span class="abs nav" style="left:694px">WHY I DO IT &amp; HOW I DO IT</span>
    <span class="abs nav" style="left:910px">ABOUT ME</span>
    <span class="abs nav" style="left:1032px">CONTACT</span>
  </nav>
</header>

<section class="hero" role="img" aria-label="Night view of a riverside city skyline with a TV tower and modern buildings">
  <h1 class="abs hero-title">EXPERT FOR COMPANY VALUATIONS</h1>
  <p class="abs hero-sub">Sie benötigen ein Gutachten zur Ermittlung des<br>Wertes Ihres Unternehmens</p>
</section>

<section class="why">
  <h2 class="abs heading">WHY CHOOSE US</h2>
  <div class="rule" style="left:565px;top:107px;width:70px"></div>

  <div class="abs card" style="left:111px">
    <div class="badge">
      <svg width="116" height="116" viewBox="0 0 116 116"><path d="M36 60 L82 38 L68 80 L58 66 Z M58 66 L82 38" fill="none" stroke="#fff" stroke-width="3" stroke-linejoin="round"/></svg>
    </div>
    <h3>SCHNELL</h3>
    <p>Sie bekommen Ihr Gutachten zeitnah (innerhalb von max. 21 Tagen nach Zugang aller benötigten Unterlagen)</p>
  </div>

  <div class="abs card" style="left:446px">
    <div class="badge">
      <svg width="116" height="116" viewBox="0 0 116 116"><circle cx="58" cy="58" r="26" fill="none" stroke="#fff" stroke-width="3"/><path d="M46 58 L55 67 L71 49" fill="none" stroke="#fff" stroke-width="4" stroke-linecap="round" stroke-linejoin="round"/></svg>
    </div>
    <h3>ZERTIFIZIERT</h3>
    <p>Sie erhalten ein qualifiziertes und belastbares Gutachten von einem zertifizierten, anerkannten Experten</p>
  </div>

  <div class="abs card" style="left:781px">
    <div class="badge">
      <svg width="116" height="116" viewBox="0 0 116 116"><path d="M42 32 H66 L76 42 V84 H42 Z" fill="none" stroke="#fff" stroke-width="3" stroke-linejoin="round"/><path d="M49 52 H69 M49 60 H69 M49 68 H69 M49 76 H62" stroke="#fff" stroke-width="2.5"/></svg>
    </div>
    <h3>VERSTÄNDLICH</h3>
    <p>Ihr Gutachten wird für Sie logisch und nachvollziehbar sein und kein „Fachchinesisch“ enthalten</p>
  </div>
</section>

<section class="reasons">
  <div class="abs photo" role="img" aria-label="Portrait of the valuation expert in a white shirt leaning on a railing"></div>
  <h2 class="abs">WHAT DO YOU NEED OR</h2>
  <h4 class="abs">CAN USE A REPORT FOR</h4>
  <div class="abs reason" style="top:215px"><b>Reason 1</b> : Buying/selling shares or entire companies</div>
  <div class="abs reason" style="top:276px"><b>Reason 2</b> : Inheritance matters</div>
  <div class="abs reason" style="top:340px"><b>Reason 3</b> : Questions in gain compensations (in divorce)</div>
</section>

<section class="quality">
  <div class="abs art" role="img" aria-label="Illustration of a smartphone with a thumbs-up and golden stars"></div>
  <h2 class="abs heading">MY QUALITY PROMISE</h2>
  <div class="rule" style="left:568px;top:124px;width:70px"></div>
  <p class="abs small p1">Should the advised date for the preparation of the report be exceeded, you will receive the report free of charge.</p>
  <div class="abs btn-outline" style="top:207px;width:122px">I WAIVE MY FEE</div>
  <p class="abs small p2">Mein Qualitätsversprechen: Sollte der avisierte Termin für die Erstellung des Gutachtens überschritten werden, erhalten Sie das Gutachten absolut kostenfrei!</p>
  <div class="abs btn-outline" style="top:335px;width:250px">ICH VERZICHTE AUF MEIN HONORAR</div>
</section>

<section class="about">
  <div class="abs portrait" role="img" aria-label="Black and white photo of the expert in a suit on a city street"></div>
  <div class="abs card">
    <h2 class="abs heading">ABOUT ME</h2>
    <div class="rule bar"></div>
    <p class="abs txt" style="top:125px">Sed ut perspiciatis unde omnis iste natus error sit voluptatem accusantium doloremque laudantium, totam rem aperiam, eaque ipsa quae ab illo inventore veritatis et quasi architecto beatae vitae dicta sunt explicabo. Nemo enim ipsam voluptatem quia voluptas sit aspernatur aut odit aut fugit, sed quia consequuntur magni dolores eos qui ratione voluptatem sequi nesciunt.</p>
    <p class="abs txt" style="top:270px">Nemo enim ipsam voluptatem quia voluptas sit aspernatur aut odit aut fugit, sed quia consequuntur magni dolores eos qui ratione voluptatem sequi nesciunt.</p>
  </div>
</section>

<section class="circles">
  <svg class="abs" width="400" height="400" viewBox="0 0 400 400" aria-label="What, how, why circles">
    <circle cx="201" cy="206" r="197" fill="#173f8a"/>
    <circle cx="201" cy="236" r="170" fill="#2a8fc8"/>
    <circle cx="201" cy="273" r="131" fill="#6ac5c5"/>
    <circle cx="201" cy="396" r="5" fill="#fff"/>
    <g font-family="Montserrat, sans-serif" font-size="21" font-weight="600" fill="#fff" text-anchor="middle">
      <text x="201" y="62">WHAT</text>
      <text x="201" y="126">HOW</text>
      <text x="201" y="193">WHY</text>
    </g>
  </svg>
  <div class="abs wh" style="top:68px">
    <h2 class="heading">WHAT I DO</h2>
    <p style="margin-top:14px;width:460px">Conducting business valuations in case of ... Durchführung von Unternehmens-bewertungen (Wertermittlung) bei</p>
  </div>
  <div class="abs wh" style="top:198px">
    <h2 class="heading">HOW I DO</h2>
    <p style="margin-top:14px;width:460px">Jedes Gutachten beginnt mit Verstehen. Also stelle ich Ihnen Fragen und höre sehr genau zu, ihr Gutachten jedes Gutachtens fängt mit einem</p>
  </div>
  <div class="abs wh" style="top:340px">
    <h2 class="heading">WHY I DO</h2>
    <p style="margin-top:10px;width:480px">Economy is my passion. Economy is made in numbers. Sometimes it is difficult to find the right numbers. I am always interested in finding out, how economy</p>
  </div>
</section>

<section class="contact">
  <h2 class="abs heading">CONTACT US</h2>
  <div class="rule" style="left:565px;top:84px;width:70px"></div>
  <p class="abs intro">Sed ut perspiciatis unde omnis iste natus error sit voluptatem accusantium doloremque laudantium, totam remte<br>inventore veritatis et quasi architecto beatae vitae dicta sunt explicabo.</p>
  <div class="abs field" style="left:294px;top:180px;width:300px;height:44px">First Name :</div>
  <div class="abs field" style="left:606px;top:180px;width:300px;height:44px">Last Name :</div>
  <div class="abs field" style="left:294px;top:233px;width:300px;height:43px">Phone :</div>
  <div class="abs field" style="left:606px;top:233px;width:300px;height:43px">Email :</div>
  <div class="abs field" style="left:294px;top:285px;width:612px;height:59px">Message :</div>
  <div class="abs submit">SUBMIT</div>
</section>

<section class="promise">
  <div class="abs mark">LUKAS ARNHOLD</div>
  <h3 class="abs">MEIN QUALITÄTSVERSPRECHEN:</h3>
  <p class="abs">Sollte der awisierte Termin für die Erstellung des Gutachtens überschritten<br>werden, erhalten Sie das Gutachten absolut kostenfrei!<br>(Ich verzichte auf mein Honorar)</p>
</section>

<footer class="site-footer">
  <div class="abs mark">LUKAS ARNHOLD</div>
  <p class="abs copy">© Copyrights 2018 · Lukas Arnhold All Rights Reserved.</p>
  <span class="abs tag">C2</span>
</footer>

</body>
</html>
```